Business Cards for new orthopaedic surgery practice

My husband and I are starting our own orthopaedic surgery practice. We are looking for a business card that is uniform, but one will have my name/title and the other will have his. You can just create one design with my name on it for now. But when I choose your design as the winning design I will ask that you add another copy with his name/title.

We are looking for classy, simple, elite all in one. We like dark blues/a little gold/yellow. Something that goes with our logo. We want our logo incorporated. Here is all the info you need:
Business name: RV Bone & Vitality Center
Location: 38517 North Willowmere Ave
Willow Bend, FL 33412
Phone: 954-218-4063
Fax: 954-582-7341
Email: info@myrvbonecare.example

Names: Lydia Vance, M.D.
Board Certified Hand and Upper Extremity Surgeon

Ebo Dansu, M.D.
Board Certified Hip & Knee Replacement/General Orthopaedic Surgeon

Can decide what you want to put on the back. Maybe a slogan:
Grounded in Care. Centered on You

I am just going to upload our logo. The only thing is if we select you as the winning design, the location, and phone numbers may change. We will need your help to update that once fully solidified.

Industry/Entity Type

Medical

Contact Information for Business Card

Colors
0054AA
0677BA
7BADD7
CADEEF
E8F1F8
0094D4
00A9DD
6FCCEA
C7EBF8
E9F6FB

Requirements
Must have
• class, appeal,
Should not have
• We want to air on the side of masculine if we are looking at masculine vs. feminine feel. But we still want it classy, sophisticated, and something we will love

```html
<!DOCTYPE html>
<html lang="en">
<head>
<meta charset="utf-8">
<title>RV Bone &amp; Vitality Center — Business Card</title>
<link rel="stylesheet" href="https://fonts.googleapis.com/css2?family=Cinzel:wght@600;700&family=Arimo:wght@400&display=swap">
<style>
  :root {
    --navy: #1f2d5c;
    --navy-deep: #1c2852;
    --navy-top: #26375f;
    --gold: #c9a15a;
    --ink: #2b2b2b;
    --paper: #ffffff;
    --backdrop: #e4e4e4;
  }
  * { box-sizing: border-box; margin: 0; padding: 0; }
  html, body { width: 1200px; height: 1200px; overflow: hidden; }
  body { background: var(--backdrop); position: relative; font-family: "Arimo", Arial, sans-serif; }

  .card { position: absolute; width: 688px; height: 393px; overflow: hidden; }
  .card-front { left: 267px; top: 159px; background: var(--paper); }
  .card-back { left: 262px; top: 653px; background: linear-gradient(180deg, var(--navy-top), var(--navy-deep)); }

  .brand-small { position: absolute; left: 36px; top: 54px; display: flex; align-items: center; gap: 10px; }
  .brand-dot { width: 14px; height: 14px; border-radius: 50%; background: var(--gold); flex: none; }
  .brand-small-name { font-family: "Cinzel", Georgia, serif; font-weight: 600; font-size: 15px; line-height: 1.25; color: var(--navy); width: 130px; }

  .person { position: absolute; left: 35px; top: 155px; }
  .person-name { font-family: "Cinzel", Georgia, serif; font-weight: 700; font-size: 22px; color: var(--navy); letter-spacing: 0.5px; white-space: nowrap; }
  .person-title { margin-top: 4px; font-size: 15px; line-height: 19px; color: var(--gold); }

  .address { position: absolute; left: 35px; top: 236px; font-size: 15.5px; line-height: 21px; color: var(--ink); }

  .contacts { position: absolute; left: 35px; top: 294px; list-style: none; font-size: 15.5px; color: var(--ink); }
  .contacts li { display: flex; align-items: center; gap: 11px; height: 20.5px; white-space: nowrap; }
  .contacts svg { width: 15px; height: 15px; fill: var(--navy); flex: none; }

  .brand-large { position: absolute; right: 34px; top: 90px; width: 330px; text-align: right;
    font-family: "Cinzel", Georgia, serif; font-weight: 700; color: var(--navy); font-size: 46px; line-height: 1.12; }

  .back-emblem { position: absolute; left: 50%; top: 78px; width: 208px; height: 208px; margin-left: -104px;
    border: 2px solid var(--gold); border-radius: 50%; display: flex; align-items: center; justify-content: center; }
  .back-emblem-name { font-family: "Cinzel", Georgia, serif; font-weight: 700; font-size: 22px; line-height: 1.2;
    color: var(--paper); text-align: center; width: 160px; }
  .slogan { position: absolute; left: 0; right: 0; top: 335px; text-align: center; font-size: 15px;
    letter-spacing: 3px; color: var(--gold); white-space: nowrap; }
</style>
</head>
<body>
  <section class="card card-front">
    <div class="brand-small">
      <span class="brand-dot"></span>
      <span class="brand-small-name">RV Bone &amp; Vitality Center</span>
    </div>

    <div class="person">
      <h1 class="person-name">LYDIA VANCE, M.D.</h1>
      <p class="person-title">Board Certified Hand and<br>Upper Extremity Surgeon</p>
    </div>

    <p class="address">38517 North Willowmere Ave<br>Willow Bend, FL 33412</p>

    <ul class="contacts">
      <li><svg viewBox="0 0 16 16"><path d="M3.6 1.2l2.3 2.6-1.3 1.9c.9 2 2.4 3.6 4.5 4.6l1.9-1.3 2.6 2.3-1.2 2.3C7.6 15 1.3 8.7.9 3.1z"/></svg>954-218-4063</li>
      <li><svg viewBox="0 0 16 16"><path d="M4 1h7l1 1v4H4z M1 7h14v6H1z M3 13h10v2H3z"/></svg>954-582-7341</li>
      <li><svg viewBox="0 0 16 16"><path d="M1 3h14v10H1z" fill="none" stroke="#1f2d5c" stroke-width="1.6"/><path d="M1.5 3.5L8 9l6.5-5.5" fill="none" stroke="#1f2d5c" stroke-width="1.6"/></svg>info@myrvbonecare.example</li>
      <li><svg viewBox="0 0 16 16"><circle cx="8" cy="8" r="7"/><path d="M5 4c2 1 1 3 3 3s1 3 3 4M9 2c-1 2 2 2 3 3" fill="none" stroke="#fff" stroke-width="1.4"/></svg>www.myrvbonecare.example</li>
    </ul>

    <p class="brand-large">RV Bone &amp;<br>Vitality<br>Center</p>
  </section>

  <section class="card card-back">
    <div class="back-emblem">
      <span class="back-emblem-name">RV Bone &amp; Vitality Center</span>
    </div>
    <p class="slogan">GROUNDED IN CARE. CENTERED ON YOU</p>
  </section>
</body>
</html>
```